Renny Oskow - Free Personalised Health Consultation - "One size does not fit all"

This flyer will be left on tables/seats at speaking events and seminars and used to attain leads.

Top half will have "SMS me for a FREE Personalised Health Consultation" and my picture (see www.rennyoskow-demo.com and pick most engaging photo) and underneath my contact details. It must have lines with "Notes:" halfway down so people can take notes at the seminar and lines on the back with my contact details again and "Notes: with lines.

I am having a business card also being designed by Artvane for same and would like the flyer and business card to carry a similar feel/look for consistency.

Below is the brief for the business card being designed:
Business Card for www.rennyoskow-demo.com site. It is a trust site and I use it for 1:1 relatable connections. It is the one I use for building intimate 1:1 trust building and Exec Coaching Services and programs for high wealth individuals and corporates. I also have a commercial programmatic site of my personal health products and services and programs for main stream one to many. www.steadyforwardliving-demo.com that can also provoke thought for the www.rennyoskow-demo.com business card. (mind you will get a separate business card for that site, but want to provide context). It has a logo which you may want to draw from in designing the rennyoskow business card which is personal and is about building my brand. There is also a rennyoskow personal PX page and rennyoskow business PX page. I am a Certified Talent Compass 3.1 Coach with Norvik and you can get a corporate brief of me on there to give you more context https://www.norvikcoachhub-demo.com/coach/en-us/directory?search=renny

Target Market(s)

Exec, IT, Health conscious. Corporates wanting to run Health and Wellness programs. Those wanting to go from good to great. Millennials to Middleaged.

Industry/Entity Type

Health And Wellness

Font styles to use
Sans Serif
Other font styles liked:
• Arial and Calibri ok too

Colors

Designer to choose colors to be used in the design.

Requirements
Must have
• Picture of me - use best from www.rennyoskow-demo.com or can send one you choose.
• Contact details like my buisness card being designed by you guys in separate project.
• Name: Renny Oskow
• email: renny@rennyoskow-demo.,com
• Phone: Australia +61 400 000 137 Singapore: +65 9000 2468
Nice to have
• Open to ideas

```html
<!DOCTYPE html>
<html lang="en">
<head>
<meta charset="utf-8">
<title>Renny Oskow – Free Personalised Health Consultation Flyer</title>
<link href="https://fonts.googleapis.com/css2?family=Oswald:wght@300;400;500;700&family=Open+Sans:wght@400;600&family=Tinos:wght@700&display=swap" rel="stylesheet">
<style>
  :root {
    --ink: #1f1f1f;
    --panel: #2c2c2c;
    --paper: #ffffff;
    --stage: #e9eaec;
    --rule: #8a8a8a;
    --ghost: #ececec;
    --photo-light: #d9d9d9;
    --photo-dark: #4a4a4a;
  }
  * { box-sizing: border-box; margin: 0; padding: 0; }
  html, body { width: 1200px; height: 1200px; overflow: hidden; }
  body {
    background: var(--stage);
    display: flex;
    align-items: center;
    justify-content: center;
    gap: 40px;
    font-family: "Open Sans", Arial, sans-serif;
    color: var(--ink);
  }
  .flyer {
    position: relative;
    width: 560px;
    height: 737px;
    background: var(--paper);
    box-shadow: 0 2px 10px rgba(0,0,0,0.12);
    overflow: hidden;
  }

  /* Front hero */
  .hero { display: flex; height: 462px; }
  .hero-photo {
    width: 262px;
    height: 100%;
    background: linear-gradient(160deg, var(--photo-light) 0%, #bdbdbd 35%, var(--photo-dark) 70%, #9a9a9a 100%);
  }
  .hero-panel {
    flex: 1;
    background: var(--panel);
    color: var(--paper);
    position: relative;
    padding: 78px 0 0 14px;
    font-family: "Oswald", "Arial Narrow", sans-serif;
  }
  .offer-lead { font-weight: 300; font-size: 37px; line-height: 1; letter-spacing: -0.5px; }
  .offer-free { font-weight: 500; font-size: 128px; line-height: 1.02; letter-spacing: -2px; margin-left: -2px; }
  .offer-kind { font-weight: 300; font-size: 44px; line-height: 1; letter-spacing: -0.5px; }
  .offer-service {
    display: inline-block;
    margin-top: 8px;
    background: var(--paper);
    color: var(--ink);
    font-weight: 700;
    font-size: 27px;
    line-height: 1;
    padding: 6px 6px 7px;
    letter-spacing: -0.3px;
  }
  .signature {
    position: absolute;
    right: 22px;
    bottom: 40px;
    font-family: "Tinos", "Times New Roman", serif;
    font-weight: 700;
    font-size: 20px;
    letter-spacing: 0.5px;
  }

  /* Notes */
  .notes-label { font-size: 13px; font-weight: 600; letter-spacing: 0.3px; }
  .notes-lines { list-style: none; }
  .notes-lines li { height: 30px; border-bottom: 1px solid var(--rule); }
  .front .notes { padding: 30px 28px 0 22px; }
  .front .notes-lines { margin-top: -6px; }

  /* Contact band */
  .contact-band {
    position: absolute;
    left: 0; right: 0; bottom: 30px;
    height: 24px;
    background: var(--panel);
    color: var(--paper);
    display: flex;
    align-items: center;
    justify-content: space-between;
    padding: 0 22px;
    font-size: 11px;
    font-weight: 600;
  }
  .contact-item { display: flex; align-items: center; gap: 4px; white-space: nowrap; }
  .contact-item svg { width: 9px; height: 9px; fill: var(--paper); }

  /* Back */
  .back-ghost {
    position: absolute;
    left: 60px; right: 40px; top: 10px; bottom: 54px;
    background: radial-gradient(ellipse at 50% 45%, var(--ghost) 0%, #f3f3f3 55%, var(--paper) 85%);
  }
  .back .notes { position: relative; padding: 24px 40px 0 28px; }
  .back .notes-lines { margin-top: 4px; }
  .back .notes-lines li { height: 31px; }
</style>
</head>
<body>

  <section class="flyer front" aria-label="Flyer front">
    <div class="hero">
      <div class="hero-photo" role="img" aria-label="Black and white photo of Renny Oskow in a suit, leaning on a bench in a bright arcade"></div>
      <div class="hero-panel">
        <p class="offer-lead">SMS me for a</p>
        <p class="offer-free">FREE</p>
        <p class="offer-kind">Personalised</p>
        <p class="offer-service">Health Consultation</p>
        <p class="signature">–Renny Oskow</p>
      </div>
    </div>
    <div class="notes">
      <p class="notes-label">NOTES</p>
      <ul class="notes-lines"><li></li><li></li><li></li><li></li><li></li></ul>
    </div>
    <footer class="contact-band">
      <span class="contact-item"><svg viewBox="0 0 10 10"><path d="M2 0.5 3.6 2.6 2.7 3.6Q3.8 5.9 6.4 7.3L7.4 6.4 9.5 8 8.2 9.5Q4.5 9 1.5 5.5 0 3.4 0.5 1.8Z"/></svg>Australia +61 400 000 137</span>
      <span class="contact-item"><svg viewBox="0 0 10 10"><path d="M2 0.5 3.6 2.6 2.7 3.6Q3.8 5.9 6.4 7.3L7.4 6.4 9.5 8 8.2 9.5Q4.5 9 1.5 5.5 0 3.4 0.5 1.8Z"/></svg>Singapore: +65 9000 2468</span>
      <span class="contact-item"><svg viewBox="0 0 10 10"><path d="M0 2H10V8.5H0Z M0.6 2.4 5 5.8 9.4 2.4" stroke="#2c2c2c" stroke-width="0.8"/></svg>renny@rennyoskow-demo.,com</span>
    </footer>
  </section>

  <section class="flyer back" aria-label="Flyer back">
    <div class="back-ghost" role="img" aria-label="Faint background photo of Renny Oskow with arms crossed"></div>
    <div class="notes">
      <p class="notes-label">NOTES</p>
      <ul class="notes-lines">
        <li></li><li></li><li></li><li></li><li></li><li></li><li></li>
        <li></li><li></li><li></li><li></li><li></li><li></li><li></li>
        <li></li><li></li><li></li><li></li><li></li><li></li>
      </ul>
    </div>
    <footer class="contact-band">
      <span class="contact-item"><svg viewBox="0 0 10 10"><path d="M2 0.5 3.6 2.6 2.7 3.6Q3.8 5.9 6.4 7.3L7.4 6.4 9.5 8 8.2 9.5Q4.5 9 1.5 5.5 0 3.4 0.5 1.8Z"/></svg>Australia +61 400 000 137</span>
      <span class="contact-item"><svg viewBox="0 0 10 10"><path d="M2 0.5 3.6 2.6 2.7 3.6Q3.8 5.9 6.4 7.3L7.4 6.4 9.5 8 8.2 9.5Q4.5 9 1.5 5.5 0 3.4 0.5 1.8Z"/></svg>Singapore: +65 9000 2468</span>
      <span class="contact-item"><svg viewBox="0 0 10 10"><path d="M0 2H10V8.5H0Z M0.6 2.4 5 5.8 9.4 2.4" stroke="#2c2c2c" stroke-width="0.8"/></svg>renny@rennyoskow-demo.,com</span>
    </footer>
  </section>

</body>
</html>
```